Modern Business Card For A Digital Advertising Company

I'll be print on the Pell Prints Velour paper http://us.pellprints.com/products/velour/business-cards.html
Need's to be modern and use the color palette of the logo or gray scales. I think integrating the pixelation of the logo in to the card and having it wrap from one side to the other could be interesting. My company provides ad operations, web development, and number of other services to websites around the world. You can see my website at http://www.zantorhq.com
Contact info on the card needs to have
Owen Lasko
President
p.318.204.6637
owen@zantorhq.com
http://www.zantorhq.com
Doesn't necessarily need to be in that order
Website owners
Business

```html
<!DOCTYPE html>
<html lang="en">
<head>
<meta charset="utf-8">
<title>Zantor HQ Business Card</title>
<link href="https://fonts.googleapis.com/css2?family=PT+Sans:wght@400;700&family=Tinos&display=swap" rel="stylesheet">
<style>
  :root {
    --page-bg: #ecebe8;
    --card-white: #ffffff;
    --brand-green: #1e9336;
    --brand-lime: #7cc242;
    --stripe-gray: #dcdcdc;
    --ink: #111111;
    --shadow: rgba(0, 0, 0, 0.16);
  }
  html, body {
    margin: 0;
    padding: 0;
    width: 1200px;
    height: 1097px;
    overflow: hidden;
    background: var(--page-bg);
  }
  .sheet {
    position: relative;
    width: 1200px;
    height: 1097px;
  }
  .card {
    position: absolute;
    left: 180px;
    width: 840px;
    height: 480px;
    background: var(--card-white);
    overflow: hidden;
    box-shadow: 0 6px 18px var(--shadow);
  }
  .card--back { top: 45px; }
  .card--front { top: 572px; }
  .card__wave {
    position: absolute;
    inset: 0;
    width: 100%;
    height: 100%;
  }
  .brand {
    position: absolute;
    display: flex;
    align-items: center;
    gap: 14px;
    font-family: "PT Sans", sans-serif;
    font-weight: 700;
    color: var(--brand-green);
    letter-spacing: 3px;
    white-space: nowrap;
  }
  .brand__mark {
    width: 34px;
    height: 34px;
    background: var(--brand-lime);
  }
  .card--back .brand {
    left: 50%;
    top: 110px;
    transform: translateX(-50%);
    font-size: 46px;
  }
  .card--front .brand {
    left: 70px;
    top: 90px;
    font-size: 44px;
  }
  .back-url {
    position: absolute;
    left: 150px;
    top: 330px;
    font-family: "Tinos", serif;
    font-size: 30px;
    letter-spacing: 3px;
    color: var(--card-white);
    transform: rotate(9deg);
    transform-origin: left center;
  }
  .person {
    position: absolute;
    right: 60px;
    top: 150px;
    text-align: right;
  }
  .person__name {
    font-family: "Tinos", serif;
    font-size: 40px;
    color: var(--ink);
    line-height: 1;
  }
  .person__title {
    font-family: "PT Sans", sans-serif;
    font-size: 24px;
    color: var(--ink);
    margin-top: 4px;
  }
  .contacts {
    position: absolute;
    left: 438px;
    top: 250px;
    padding-left: 18px;
    border-left: 3px solid var(--brand-green);
    list-style: none;
    margin: 0;
    font-family: "PT Sans", sans-serif;
    font-size: 25px;
    color: var(--ink);
  }
  .contacts__item {
    display: flex;
    align-items: center;
    gap: 14px;
    height: 38px;
  }
  .contacts__icon {
    width: 22px;
    height: 22px;
    flex: none;
  }
</style>
</head>
<body>
<main class="sheet">

  <section class="card card--back" aria-label="Card back">
    <svg class="card__wave" viewBox="0 0 840 480" preserveAspectRatio="none" aria-hidden="true">
      <path d="M0,222 C220,170 430,290 600,372 C700,418 790,418 840,404 L840,480 L0,480 Z" fill="var(--stripe-gray)"/>
      <path d="M0,240 C220,188 430,308 600,390 C700,436 790,436 840,422 L840,480 L0,480 Z" fill="var(--brand-green)"/>
    </svg>
    <div class="brand"><span class="brand__mark"></span>ZANTOR HQ</div>
    <div class="back-url">www.zantorhq.com</div>
  </section>

  <section class="card card--front" aria-label="Card front">
    <svg class="card__wave" viewBox="0 0 840 480" preserveAspectRatio="none" aria-hidden="true">
      <path d="M0,196 C180,200 300,300 470,372 C600,428 700,470 840,480 L0,480 Z" fill="var(--stripe-gray)"/>
      <path d="M0,214 C180,218 300,318 470,390 C580,436 660,468 760,480 L0,480 Z" fill="var(--brand-green)"/>
    </svg>
    <div class="brand"><span class="brand__mark"></span>ZANTOR HQ</div>

    <div class="person">
      <div class="person__name">Owen Lasko</div>
      <div class="person__title">President</div>
    </div>

    <ul class="contacts">
      <li class="contacts__item">
        <svg class="contacts__icon" viewBox="0 0 24 24" aria-hidden="true">
          <circle cx="12" cy="12" r="10.5" fill="none" stroke="var(--brand-green)" stroke-width="1.6"/>
          <path d="M8.5 7.5 l2 0 1 3 -1.4 1 a6 6 0 0 0 2.6 2.6 l1 -1.4 3 1 0 2 a1.5 1.5 0 0 1 -1.6 1.4 A9 9 0 0 1 7 9.1 a1.5 1.5 0 0 1 1.5 -1.6z" fill="var(--brand-green)"/>
        </svg>
        <span>318-204-6637</span>
      </li>
      <li class="contacts__item">
        <svg class="contacts__icon" viewBox="0 0 24 24" aria-hidden="true">
          <rect x="3" y="6" width="18" height="12" fill="none" stroke="var(--brand-green)" stroke-width="1.6"/>
          <path d="M3 6 L12 13 L21 6" fill="none" stroke="var(--brand-green)" stroke-width="1.6"/>
        </svg>
        <span>owen@zantorhq.com</span>
      </li>
      <li class="contacts__item">
        <svg class="contacts__icon" viewBox="0 0 24 24" aria-hidden="true">
          <circle cx="12" cy="12" r="10" fill="var(--brand-green)"/>
          <g fill="none" stroke="#ffffff" stroke-width="1.2">
            <ellipse cx="12" cy="12" rx="4.5" ry="10"/>
            <line x1="2" y1="12" x2="22" y2="12"/>
            <line x1="12" y1="2" x2="12" y2="22"/>
            <path d="M4 7 H20 M4 17 H20"/>
          </g>
        </svg>
        <span>www.zantorhq.com</span>
      </li>
    </ul>
  </section>

</main>
</body>
</html>
```